Kelvaro.ch is looking for business card letterhead and envelope C5 with WOW effect

We need a strong business card for our company Kelvaro.ch, logo is available. You want a black or dark background on which the logo Stark r% 26 # 252; appears. Letterhead and envelope in C5 format should be in a similar design, but does not have to be We need a strong business card for our company Kelvaro.ch, logo is available. A black or dark background is desired, on which the logo Stark comes across. The letterhead and the envelope in C5 format should have a similar design.

Target Market(s)

Private customers as well as entrepreneurs

Contact Information for Business Card

E-mail: info@kelvaro-example.ch
Web.www.Kelvaro-example.ch
Tel: +41 ( 0 ) 79 482 6037
Adresse:
Lindenweg 14
9406 Tarnbach

Hier kann man Icons verwenden für Email,Tel und Adressse

Font styles to use
Other font styles liked:
• Dubai,bold

Colors

Designer to choose colors to be used in the design.

Requirements
Must have
• WOW effect
Nice to have
• R% 26 # 252; back business card with our service listings. - VEHICLE LABELING - SHOP WINDOW LABELING - STICKERS AND MUCH MORE ... in red color

```html
<!DOCTYPE html>
<html lang="en">
<head>
<meta charset="utf-8">
<title>Kelvaro.ch business card</title>
<link href="https://fonts.googleapis.com/css2?family=Exo+2:wght@700&family=Montserrat:wght@400;500;700&display=swap" rel="stylesheet">
<style>
  :root {
    --stage: #2b2b2c;
    --card: #161616;
    --card-edge: #0d0d0d;
    --pattern-a: #1c1c1c;
    --pattern-b: #121212;
    --ink: #f2f2f2;
    --ink-soft: #d9d9d9;
    --accent: #f5c000;
  }
  * { box-sizing: border-box; margin: 0; padding: 0; }
  html, body {
    width: 1200px; height: 913px; overflow: hidden;
    background: var(--stage);
    font-family: "Montserrat", Arial, sans-serif;
  }
  .canvas {
    width: 1200px; height: 913px;
    display: flex; flex-direction: column; align-items: center; justify-content: center;
    gap: 40px;
  }
  .card {
    position: relative;
    width: 700px; height: 400px;
    background: var(--card);
    border: 1px solid var(--card-edge);
    overflow: hidden;
  }
  .pattern-area {
    position: absolute;
    background: radial-gradient(ellipse at center, var(--pattern-a) 0%, var(--pattern-b) 75%);
  }
  .card-back .pattern-area { left: 0; bottom: 0; width: 62%; height: 62%; }
  .card-front .pattern-area { right: 0; top: 0; width: 58%; height: 80%; }

  .brand-name {
    font-family: "Montserrat", Arial, sans-serif;
    font-weight: 700;
    color: var(--ink);
    letter-spacing: 1px;
    text-transform: uppercase;
  }
  .card-back .brand-name {
    position: absolute; right: 56px; top: 56px;
    font-size: 40px;
  }
  .service-list {
    position: absolute; right: 56px; top: 120px;
    list-style: none; text-align: right;
    color: var(--ink-soft); font-size: 15px; font-weight: 500;
    line-height: 1.7; letter-spacing: 0.5px;
  }
  .service-list li::after {
    content: ""; display: inline-block;
    width: 7px; height: 7px; border-radius: 50%;
    background: var(--accent); margin-left: 10px; vertical-align: middle;
  }

  .brand-lockup {
    position: absolute; left: 56px; top: 64px;
    display: flex; align-items: center; gap: 16px;
  }
  .brand-mark { width: 40px; height: 40px; background: var(--accent); }
  .card-front .brand-name { font-size: 32px; }

  .person { position: absolute; left: 56px; top: 170px; }
  .person-name {
    font-family: "Exo 2", "Montserrat", sans-serif;
    font-weight: 700; font-size: 30px; color: var(--accent);
  }
  .person-role { color: var(--ink); font-size: 16px; font-weight: 500; margin-top: 2px; }

  .contact-list {
    position: absolute; left: 56px; top: 262px;
    list-style: none; color: var(--ink-soft);
    font-size: 15px; line-height: 27px;
  }
  .contact-list li { display: flex; align-items: center; gap: 12px; }
  .contact-icon { width: 15px; height: 15px; fill: var(--accent); flex: none; }
</style>
</head>
<body>
<main class="canvas">
  <section class="card card-back" aria-label="Business card back">
    <div class="pattern-area" role="img" aria-label="Embossed hexagon pattern in black"></div>
    <div class="brand-name">Kelvaro.ch</div>
    <ul class="service-list">
      <li>Vehicle labeling</li>
      <li>Shop window labeling</li>
      <li>Stickers</li>
    </ul>
  </section>

  <section class="card card-front" aria-label="Business card front">
    <div class="pattern-area" role="img" aria-label="Embossed hexagon pattern in black"></div>
    <div class="brand-lockup">
      <span class="brand-mark"></span>
      <span class="brand-name">Kelvaro.ch</span>
    </div>
    <div class="person">
      <div class="person-name">Daniel Berger</div>
      <div class="person-role">President</div>
    </div>
    <ul class="contact-list">
      <li>
        <svg class="contact-icon" viewBox="0 0 24 24" aria-hidden="true"><path d="M6.6 10.8a15 15 0 0 0 6.6 6.6l2.2-2.2a1 1 0 0 1 1-.25 11.4 11.4 0 0 0 3.6.57 1 1 0 0 1 1 1V20a1 1 0 0 1-1 1A17 17 0 0 1 3 4a1 1 0 0 1 1-1h3.5a1 1 0 0 1 1 1c0 1.25.2 2.45.57 3.57a1 1 0 0 1-.25 1z"/></svg>
        +41 ( 0 ) 79 482 6037
      </li>
      <li>
        <svg class="contact-icon" viewBox="0 0 24 24" aria-hidden="true"><path d="M2 5h20v14H2z M4 7v.5l8 5 8-5V7l-8 5z" fill-rule="evenodd"/></svg>
        info@kelvaro-example.ch
      </li>
      <li>
        <svg class="contact-icon" viewBox="0 0 24 24" aria-hidden="true"><path d="M12 2a10 10 0 1 0 0 20 10 10 0 0 0 0-20zm0 2c.9 1.2 1.6 2.6 2 4h-4c.4-1.4 1.1-2.8 2-4zM4.3 14a8 8 0 0 1 0-4h3.3a16 16 0 0 0 0 4zm.8 2h2.9c.4 1.3.9 2.5 1.6 3.6A8 8 0 0 1 5.1 16zM8 8H5.1a8 8 0 0 1 4.5-3.6C8.9 5.5 8.4 6.7 8 8zm4 12c-.9-1.2-1.6-2.6-2-4h4c-.4 1.4-1.1 2.8-2 4zm2.3-6H9.7a14 14 0 0 1 0-4h4.6a14 14 0 0 1 0 4zm.1 5.6c.7-1.1 1.2-2.3 1.6-3.6h2.9a8 8 0 0 1-4.5 3.6zM16.4 14a16 16 0 0 0 0-4h3.3a8 8 0 0 1 0 4zM16 8c-.4-1.3-.9-2.5-1.6-3.6A8 8 0 0 1 18.9 8z"/></svg>
        www.Kelvaro-example.ch
      </li>
      <li>
        <svg class="contact-icon" viewBox="0 0 24 24" aria-hidden="true"><path d="M12 2a7 7 0 0 0-7 7c0 5.2 7 13 7 13s7-7.8 7-13a7 7 0 0 0-7-7zm0 9.5a2.5 2.5 0 1 1 0-5 2.5 2.5 0 0 1 0 5z"/></svg>
        Lindenweg 14 9406 Tarnbach
      </li>
    </ul>
  </section>
</main>
</body>
</html>
```